Black Matte card with samurai logo which I would like it to be textured and company name on one side and on the other side I would like the company information with the reno (Face logo) Sushi logo. Double Sided card.

majority customers are University students, University sororities and fraternities.

It Company

Reno Sushi
317 W. Harlow Ave
Tucson, AZ 85042
Phone (520)413-6271
Fax (520)357-1846
E-mail: Renosushidesert@mailbox-example.com
FB: Renosushidesert
Twitter: Renosushidesert

• Present Normal

```html
<!DOCTYPE html>
<html lang="en">
<head>
<meta charset="utf-8">
<title>Reno Sushi – Business Card</title>
<link href="https://fonts.googleapis.com/css2?family=Open+Sans:wght@400;600&display=swap" rel="stylesheet">
<style>
  :root {
    --bg: #ece9e4;
    --card-white: #ffffff;
    --ink: #231f20;
    --text: #3d3b3c;
    --red: #b3261e;
    --rule: #c9c9c9;
    --matte-1: #2a2a2a;
    --matte-2: #121212;
    --white: #ffffff;
  }
  * { margin: 0; padding: 0; box-sizing: border-box; }
  html, body { width: 1200px; height: 1177px; overflow: hidden; }
  body {
    background: var(--bg);
    font-family: "Open Sans", Arial, sans-serif;
    position: relative;
  }
  .card {
    position: absolute;
    width: 940px;
    height: 535px;
    border-radius: 28px;
    overflow: hidden;
    box-shadow: 0 4px 14px rgba(0,0,0,0.25);
  }
  /* Front: contact side */
  .card--info { left: 30px; top: 34px; background: var(--card-white); }
  .mascot {
    position: absolute;
    border-radius: 6px;
    background: linear-gradient(160deg, #2b2b2b 0%, #1b1b1b 60%, #8e241e 100%);
  }
  .card--info .mascot { left: 130px; top: 50px; width: 216px; height: 207px; }
  .brand-name {
    position: absolute;
    left: 120px; top: 258px; width: 230px;
    text-align: center;
    color: var(--red);
    font-weight: 400;
    line-height: 1;
  }
  .brand-name .primary { display: block; font-size: 72px; }
  .brand-name .secondary { display: block; font-size: 34px; margin-top: 2px; }
  .divider {
    position: absolute;
    left: 413px; top: 108px;
    width: 1px; height: 225px;
    background: var(--rule);
  }
  .contact { position: absolute; left: 443px; top: 120px; list-style: none; }
  .contact li {
    display: flex; align-items: center;
    height: 41px;
    font-size: 22px;
    color: var(--text);
  }
  .contact svg { width: 22px; height: 22px; margin-right: 14px; flex: none; }
  .address {
    position: absolute; left: 443px; top: 282px;
    font-size: 22px; line-height: 35px; color: var(--text);
  }
  .wave { position: absolute; left: 0; top: 0; width: 940px; height: 535px; }
  .social { position: absolute; left: 642px; top: 445px; list-style: none; }
  .social li {
    display: flex; align-items: center;
    height: 40px;
    color: var(--white);
    font-size: 21px;
  }
  .social .mark {
    width: 26px; height: 26px;
    background: var(--red);
    margin-right: 10px;
  }
  /* Back: matte side */
  .card--matte {
    left: 243px; top: 611px; height: 536px;
    background: linear-gradient(180deg, var(--matte-1) 0%, var(--matte-2) 50%, var(--matte-1) 100%);
  }
  .card--matte .mascot {
    left: 311px; top: 54px; width: 324px; height: 281px;
    background: linear-gradient(160deg, #f2f2f2 0%, #3a3a3a 45%, #9c2820 100%);
  }
  .matte-name {
    position: absolute;
    left: 0; right: 0; top: 380px;
    text-align: center;
    color: var(--red);
    font-size: 82px;
    font-weight: 400;
    line-height: 1;
  }
</style>
</head>
<body>

<section class="card card--info" aria-label="Card front with contact information">
  <div class="mascot" role="img" aria-label="Samurai mascot illustration holding a sword and a fish"></div>
  <h1 class="brand-name"><span class="primary">reno</span><span class="secondary">sushi</span></h1>
  <div class="divider"></div>

  <ul class="contact">
    <li>
      <svg viewBox="0 0 24 24"><circle cx="12" cy="12" r="10.5" fill="none" stroke="var(--red)" stroke-width="2"/><path d="M8.5 7c-.8.6-1 2 0 4s3 4 4.5 5c1 .6 2.2.5 2.8-.3l-1.8-1.8-1.2.8c-1-.6-2.4-2-3-3l.8-1.2L8.5 7z" fill="var(--red)"/></svg>
      (520)413-6271
    </li>
    <li>
      <svg viewBox="0 0 24 24"><rect x="7" y="2" width="10" height="20" rx="2" fill="var(--red)"/><rect x="9" y="5" width="6" height="7" fill="#fff"/><rect x="9" y="14" width="6" height="5" fill="#fff" opacity=".6"/></svg>
      (520)357-1846
    </li>
    <li>
      <svg viewBox="0 0 24 24"><rect x="2" y="5" width="20" height="14" rx="2" fill="var(--red)"/><path d="M3 6l9 7 9-7" fill="none" stroke="#fff" stroke-width="1.6"/></svg>
      Renosushidesert@mailbox-example.com
    </li>
  </ul>

  <p class="address">317 W. Harlow Ave Tucson<br>AZ 85042</p>

  <svg class="wave" viewBox="0 0 696 396" preserveAspectRatio="none" aria-hidden="true">
    <path d="M0 352 C180 330 430 300 696 328 L696 396 L0 396 Z" fill="var(--ink)"/>
    <path d="M0 347 C180 324 430 292 696 320" fill="none" stroke="var(--ink)" stroke-width="3"/>
    <path d="M0 371 C150 360 330 335 460 318 C340 350 170 375 0 392 Z" fill="var(--red)"/>
    <path d="M0 356 C180 336 430 306 696 333" fill="none" stroke="#fff" stroke-width="3"/>
  </svg>

  <ul class="social">
    <li><span class="mark"></span>Renosushidesert</li>
    <li><span class="mark"></span>Renosushidesert</li>
  </ul>
</section>

<section class="card card--matte" aria-label="Card back with mascot and name">
  <div class="mascot" role="img" aria-label="Samurai mascot illustration holding a sword and a fish"></div>
  <h2 class="matte-name">reno sushi</h2>
</section>

</body>
</html>
```